Album Cover for upcoming release

Hi, I need an album cover for a song that I’ll be releasing soon. The album cover must contain the title of the song, which is:

Carry the Moon (remix)

The album cover must also contain the artist name:

Owen Tarrick

The song is a remix of a song that I released in late-May called “Carry the Moon.” I wrote the original song for my wife. If you’re interested, please give it a listen on Velvo Tunes or Rumblewave under the artist Owen Tarrick. Here’s a Rumblewave link to the original song (it already has more than 175,000 streams):

https://play.rumblewave.example/track/7RbTqZ82KXN3pLmWcVoHeF?si=ztGd4NfQxWYb9uRsEoPaMc

The remix is VERY, VERY different! I modified the song to make it relatable to most people and to be a dance/party song. Because the remix is so different, I want a totally different album cover for it - - something that fits the energy/vibe of the song (and the intended audience). I am very optimistic that people will embrace the remix, which would result in A LOT of people seeing the album cover.

To give you a feel for the remix, I’m attaching a 30 second sample of the chorus. Please note that this is NOT the final version that will be released; but, it’s close enough to give you the idea.

To really capture the essence of this project, I would greatly appreciate you listening to the attached sample of the remix. Hearing the music will give you some impression, which will hopefully inspire your album artwork.

Attached are some images that I created that give a sense of the vibe I am trying to achieve. Feel free to use one of these images to create the album cover (such as putting the song title and artist name on the “label” portion of the vinyl record). But, you are NOT required to use one os these images.
Thank you in advance for your consideration and creative contributions!

Target Market(s)

Dance and party crowd; night clubs, sporting events, weddings

Font styles to use
Sans Serif

Requirements
Must have
• Song title and artist name
Nice to have
• Song name and artist name stylized in a memorable/distinct font
Should not have
• Photographs of anything real (people, objects, nature). Animated can be fine

```html
<!DOCTYPE html>
<html lang="en">
<head>
<meta charset="utf-8">
<title>Carry the Moon (remix) — Owen Tarrick</title>
<link rel="stylesheet" href="https://fonts.googleapis.com/css2?family=Playfair+Display+SC:wght@700;900&family=Oswald:wght@600&family=Archivo+Black&display=swap">
<style>
  :root {
    --sky-deep: #2a1a8a;
    --sky-violet: #6a2bc4;
    --sky-blue: #1e7fe0;
    --sky-cyan: #35c6f2;
    --sun-pink: #f2487e;
    --sun-orange: #ff8a1f;
    --glow-yellow: #ffd21a;
    --sea-teal: #1f6f94;
    --sea-navy: #0d2446;
    --ink-white: #ffffff;
    --outline-blue: #1aa3e6;
    --shade-navy: #1b2a6b;
  }
  * { margin: 0; padding: 0; box-sizing: border-box; }
  html, body { width: 1200px; height: 1200px; overflow: hidden; background: var(--sea-navy); }
  .cover {
    position: relative;
    width: 1200px;
    height: 1200px;
    overflow: hidden;
  }
  .cover-art {
    position: absolute;
    inset: 0;
    width: 1200px;
    height: 1200px;
    display: block;
  }
  .song-title {
    position: absolute;
    left: 60px;
    right: 60px;
    top: 104px;
    text-align: center;
    font-family: "Playfair Display SC", "Times New Roman", serif;
    font-weight: 900;
    font-size: 100px;
    line-height: 1;
    letter-spacing: 1px;
    color: var(--ink-white);
    text-shadow:
      3px 3px 0 var(--shade-navy),
      -1px -1px 0 var(--shade-navy),
      1px -1px 0 var(--shade-navy),
      -1px 1px 0 var(--shade-navy);
    white-space: nowrap;
  }
  .remix-word {
    position: absolute;
    left: 0;
    right: 0;
    top: 555px;
    text-align: center;
    font-family: "Oswald", "Arial Narrow", sans-serif;
    font-weight: 600;
    font-size: 300px;
    line-height: 1;
    letter-spacing: 8px;
    padding-left: 8px;
    color: var(--ink-white);
    -webkit-text-stroke: 5px var(--outline-blue);
    paint-order: stroke fill;
  }
  .remix-reflection {
    position: absolute;
    left: 0;
    right: 0;
    top: 829px;
    height: 90px;
    overflow: hidden;
    text-align: center;
    opacity: 0.35;
  }
  .remix-reflection span {
    display: block;
    font-family: "Oswald", "Arial Narrow", sans-serif;
    font-weight: 600;
    font-size: 300px;
    line-height: 1;
    letter-spacing: 8px;
    padding-left: 8px;
    color: var(--ink-white);
    transform: scaleY(-1);
    transform-origin: 50% 50%;
    -webkit-mask-image: linear-gradient(to top, rgba(0,0,0,1), rgba(0,0,0,0) 30%);
            mask-image: linear-gradient(to top, rgba(0,0,0,1), rgba(0,0,0,0) 30%);
  }
  .artist-name {
    position: absolute;
    left: 0;
    right: 0;
    top: 1088px;
    text-align: center;
    font-family: "Archivo Black", "Arial Black", sans-serif;
    font-size: 32px;
    line-height: 1;
    letter-spacing: 25px;
    padding-left: 25px;
    color: var(--ink-white);
    white-space: nowrap;
  }
</style>
</head>
<body>
  <main class="cover">
    <svg class="cover-art" viewBox="0 0 1200 1200" role="img" aria-label="Illustration: radiant burst of neon light rays over a glowing pink sunset, two vinyl records standing on the horizon, shimmering ocean below">
      <defs>
        <radialGradient id="sky-burst" cx="600" cy="780" r="900" gradientUnits="userSpaceOnUse">
          <stop offset="0" stop-color="var(--glow-yellow)"/>
          <stop offset="0.18" stop-color="var(--sky-cyan)"/>
          <stop offset="0.45" stop-color="var(--sky-blue)"/>
          <stop offset="0.75" stop-color="var(--sky-violet)"/>
          <stop offset="1" stop-color="var(--sky-deep)"/>
        </radialGradient>
        <radialGradient id="sun-glow" cx="600" cy="430" r="240" gradientUnits="userSpaceOnUse">
          <stop offset="0" stop-color="var(--sun-orange)"/>
          <stop offset="0.6" stop-color="var(--sun-pink)" stop-opacity="0.8"/>
          <stop offset="1" stop-color="var(--sun-pink)" stop-opacity="0"/>
        </radialGradient>
        <linearGradient id="sea" x1="0" y1="832" x2="0" y2="1200" gradientUnits="userSpaceOnUse">
          <stop offset="0" stop-color="var(--sea-teal)"/>
          <stop offset="0.5" stop-color="var(--sun-orange)" stop-opacity="0.8"/>
          <stop offset="1" stop-color="var(--sea-navy)"/>
        </linearGradient>
      </defs>
      <rect width="1200" height="832" fill="url(#sky-burst)"/>
      <rect width="1200" height="832" fill="url(#sun-glow)"/>
      <rect y="832" width="1200" height="368" fill="url(#sea)"/>
    </svg>

    <h1 class="song-title">CARRY THE MOON</h1>
    <div class="remix-word">REMIX</div>
    <div class="remix-reflection" aria-hidden="true"><span>REMIX</span></div>
    <p class="artist-name">OWEN TARRICK</p>
  </main>
</body>
</html>
```